Helen's 40th Invitation

I need an invitation designed for a 40th birthday in Singapore. The theme is a "long lunch", set in a colonial garden (black and white house - Singapore style if you want to Google or Bing it).
Look and feel should be simple, elegant, stylish, bold, fresh, minimalist. Nothing fussy, intricate, formal or too colourful. No intials, not wedding-like, minimal colour (no golds).
Setting will be garden setting with champagne, white marquee, white table cloths, long trestle tables, fresh white floowers (lilys or hydrangas).
Format should be PC friendly (jpeg, gif, pdf etc).
Size is flexible to accomodate design - it will be emailed as an attachment.
Details to include:
- Saturday, 27th November, 2010
Time - From 1pm.
Address - 214 Fernbrook Rise, Singapore
Dress: Garden Glam
RSVP - jolwen@quarlixmail.com by 13 November, 2010

```html
<!DOCTYPE html>
<html lang="en">
<head>
<meta charset="utf-8">
<title>Helen's 40th – Long Lunch Invitation</title>
<link rel="stylesheet" href="https://fonts.googleapis.com/css2?family=Roboto:wght@400;700&family=Playfair+Display:wght@400&display=swap">
<style>
  :root {
    --page: #ffffff;
    --bark: #3b2314;
    --leaf-deep: #137a44;
    --leaf-soft: #5fa37d;
    --ink: #ffffff;
  }
  * { margin: 0; padding: 0; box-sizing: border-box; }
  html, body {
    width: 1200px;
    height: 900px;
    overflow: hidden;
    background: var(--page);
  }
  .canvas {
    position: relative;
    width: 1200px;
    height: 900px;
    background: var(--page);
  }
  .invitation {
    position: absolute;
    left: 70px;
    top: 164px;
    width: 1056px;
    height: 536px;
    background: var(--bark);
    overflow: hidden;
    color: var(--ink);
    font-family: "Roboto", "Helvetica Neue", Arial, sans-serif;
  }
  .vine-art {
    position: absolute;
    left: 0;
    top: 60px;
    width: 1056px;
    height: 476px;
  }
  .details {
    position: absolute;
    right: 626px;
    top: 34px;
    text-align: right;
    font-size: 25px;
    line-height: 36px;
  }
  .details p + p { margin-top: 16px; }
  .details strong, .rsvp strong { font-weight: 700; }
  .rsvp {
    position: absolute;
    left: 544px;
    top: 86px;
    font-size: 25px;
    line-height: 36px;
  }
  .honoree {
    position: absolute;
    left: 718px;
    top: 290px;
    font-family: "Roboto", "Helvetica Neue", Arial, sans-serif;
    font-size: 46px;
    font-weight: 400;
    letter-spacing: 0.5px;
  }
  .title {
    position: absolute;
    left: 0;
    top: 0;
    width: 1056px;
    height: 536px;
  }
  .title text {
    font-family: "Playfair Display", "Bodoni Moda", Georgia, serif;
    font-size: 150px;
    fill: var(--ink);
  }
</style>
</head>
<body>
<div class="canvas">
  <section class="invitation">
    <svg class="vine-art" viewBox="0 0 1056 476" role="img" aria-label="Green climbing vine with curling tendrils and leaves sweeping across the card">
      <defs>
        <radialGradient id="vineGlow" cx="0.5" cy="0.65" r="0.6">
          <stop offset="0" stop-color="#137a44" stop-opacity="0.55"/>
          <stop offset="0.6" stop-color="#5fa37d" stop-opacity="0.25"/>
          <stop offset="1" stop-color="#5fa37d" stop-opacity="0"/>
        </radialGradient>
      </defs>
      <rect x="0" y="0" width="1056" height="476" fill="url(#vineGlow)"/>
    </svg>

    <div class="details">
      <p>Saturday, <strong>27th Nov 2010</strong><br>From <strong>1pm</strong></p>
      <p><strong>VENUE</strong> 214 Fernbrook Rise<br>Singapore</p>
      <p>Dress <strong>Garden Glam</strong></p>
    </div>

    <div class="rsvp">
      <p><strong>RSVP</strong><br>jolwen@quarlixmail.com<br>by <strong>13th Nov 2010</strong></p>
    </div>

    <p class="honoree">Helen's 40th</p>

    <svg class="title" viewBox="0 0 1056 536" aria-label="Long Lunch">
      <text x="20" y="528" textLength="1016" lengthAdjust="spacingAndGlyphs">LONG LUNCH</text>
    </svg>
  </section>
</div>
</body>
</html>
```